Wordpress theme website for professionals working together

My partner and I are offering business services, my wife in the energy business as mainly as member of the board of commissioners. I am working as interim manager/consultant in the accounting and finance area. Both activities are connected in one company VELMOT BV (dutch ltd). We need a CV based website. Beside this we do some financial and accounting services.

Target Market(s)

small medium business

Font styles to use
Sans Serif

Colors

Designer to choose colors to be used in the design.

Requirements
Must have
• Pictures of both members.
• CLEAN AND SIMPLE
• I LIKE BLACK & WHITE
Nice to have
• I like design like this theme: http://theme.pruxelo-example.com/resume/

```html
<!DOCTYPE html>
<html lang="en">
<head>
<meta charset="utf-8">
<title>VELMOT BV – Pieter &amp; Marloes</title>
<link href="https://fonts.googleapis.com/css2?family=Montserrat:wght@400;600;700&family=Open+Sans:wght@400;600;700&display=swap" rel="stylesheet">
<style>
:root{
  --ink:#1b1b1b;
  --black:#111;
  --dark:#1e1e1e;
  --tile:#2b2b2b;
  --grey:#e6e6e6;
  --light:#f3f3f3;
  --mid:#c9c9c9;
  --text:#555;
  --white:#fff;
  --brand:#2a3f8f;
}
*{box-sizing:border-box;margin:0;padding:0}
html,body{width:1200px;height:5248px;overflow:hidden}
body{font-family:"Open Sans",Arial,sans-serif;color:var(--ink);background:var(--white);font-size:12px;line-height:1.6}
h1,h2,h3,h4{font-family:"Montserrat",Arial,sans-serif}
section,header,footer{position:relative;width:1200px;overflow:hidden}
.section-title{position:absolute;left:0;width:1200px;text-align:center;font-size:28px;font-weight:700;letter-spacing:1px}
.intro{position:absolute;left:320px;width:560px;text-align:center;font-size:11px;color:var(--text);line-height:1.7}
.photo{position:absolute}

/* nav */
.site-header{height:60px;background:var(--white);border-bottom:1px solid var(--grey)}
.brand{position:absolute;left:171px;top:14px;display:flex;align-items:center;gap:8px;font-family:"Montserrat",sans-serif;font-weight:700;font-size:24px;color:var(--brand)}
.brand-mark{width:14px;height:14px;background:var(--brand)}
.main-nav{position:absolute;right:175px;top:22px;display:flex;gap:26px;font-family:"Montserrat",sans-serif;font-size:11px;letter-spacing:.5px;color:#444}
.main-nav .active{color:var(--black);font-weight:600}

/* hero */
.hero{height:563px;background:linear-gradient(90deg,#f2f2f2 0%,#e4e4e4 50%,#cfcfcf 100%)}
.hero .photo{left:612px;top:0;width:588px;height:563px;background:linear-gradient(120deg,#d6d6d6 0%,#8a8a8a 55%,#3a3a3a 100%)}
.person-name{position:absolute;left:171px;font-size:44px;font-weight:400;letter-spacing:3px}
.person-bio{position:absolute;left:171px;width:400px;font-size:11.5px;color:#333;line-height:1.75}

/* experience */
.experience{height:665px;background:linear-gradient(180deg,#eee 0%,#fff 30%)}
.timeline-line{position:absolute;left:595px;top:125px;width:2px;height:515px;background:#333}
.tl-icon{position:absolute;left:576px;width:40px;height:40px;border-radius:50%;background:var(--white);border:2px solid #333;display:flex;align-items:center;justify-content:center}
.tl-label{position:absolute;height:22px;padding:0 10px;background:var(--dark);color:var(--white);font-size:10.5px;line-height:22px;font-weight:600}
.tl-text{position:absolute;width:300px;font-size:10.5px;color:var(--text);line-height:1.6}

/* jobs */
.jobs{height:532px;background:var(--white)}
.jobs-title span{color:var(--ink);font-weight:700}
.col-title{position:absolute;font-family:"Montserrat",sans-serif;font-size:15px;font-weight:600}
.col-line{position:absolute;width:2px;background:var(--mid)}
.job-name{position:absolute;font-family:"Montserrat",sans-serif;font-size:14px;font-weight:600;line-height:1.3;width:140px}
.job-dot{position:absolute;width:10px;height:10px;border-radius:50%;border:2px solid var(--mid);background:var(--white)}
.job-text{position:absolute;width:210px;font-size:10.5px;color:var(--text);line-height:1.6}

/* skills */
.skills{height:553px;background:var(--light)}
.skill-label{position:absolute;font-family:"Montserrat",sans-serif;font-size:10.5px;font-weight:600;letter-spacing:.5px}
.skill-bar{position:absolute;height:26px;width:382px}
.skill-bar .track{position:absolute;left:0;top:0;width:362px;height:26px;background:#bdbdbd}
.skill-bar .tip{position:absolute;left:362px;top:0;width:0;height:0;border-top:13px solid transparent;border-bottom:13px solid transparent;border-left:20px solid #bdbdbd}
.skill-bar .fill{position:absolute;left:0;top:0;height:26px;background:var(--black)}
.skill-bar .pct{position:absolute;top:0;line-height:26px;font-size:10px;color:#333}

/* info tiles */
.highlights{height:437px;background:linear-gradient(180deg,#1a1a1a,#0d0d0d)}
.tile{position:absolute;top:101px;width:272px;height:231px;background:var(--tile);color:var(--white);text-align:center}
.tile svg{margin-top:42px}
.tile h4{font-size:13px;font-weight:600;letter-spacing:1px;margin-top:28px}
.tile p{font-size:12px;color:#cfcfcf;line-height:1.5;margin-top:4px}

/* portfolio */
.portfolio{height:752px;background:var(--white)}
.work{position:absolute;width:280px;height:230px}

/* partner */
.partner{height:434px;background:linear-gradient(90deg,#e9e9e9,#d9d9d9)}
.partner .photo{left:752px;top:0;width:448px;height:434px;background:linear-gradient(120deg,#cfcfcf 0%,#8b8b8b 55%,#555 100%)}
.btn-dark{position:absolute;background:var(--black);color:var(--white);font-family:"Montserrat",sans-serif;font-size:10px;font-weight:600;letter-spacing:.5px;padding:0 18px;height:30px;line-height:30px}
.notch{position:absolute;left:585px;bottom:0;width:0;height:0;border-left:15px solid transparent;border-right:15px solid transparent;border-bottom:15px solid var(--light)}

/* contact */
.contact{height:560px;background:var(--light)}
.info-block{position:absolute;left:271px;width:220px}
.info-block h4{font-size:15px;font-weight:600;display:flex;align-items:center;gap:10px}
.info-block p{font-size:10.5px;color:var(--text);line-height:1.6;padding-left:28px;margin-top:2px}
.field{position:absolute;left:542px;width:410px;height:32px;background:var(--white);border:1px solid #d4d4d4;font-size:10px;color:#888;padding:8px 10px}

/* office */
.office{height:395px;background:linear-gradient(160deg,#3f7fc4 0%,#7cb0e0 35%,#8a5a40 60%,#5a3020 100%)}
.office-title{position:absolute;left:171px;top:168px;color:var(--white);font-size:38px;font-weight:700;line-height:1.05;letter-spacing:1px}

/* footer */
.site-footer{height:297px;background:var(--black);color:var(--white)}
.f-col{position:absolute;top:52px}
.f-col h4{font-size:15px;font-weight:600;margin-bottom:10px}
.f-col p{font-size:10px;color:#aaa;line-height:1.7}
.newsletter-input{position:absolute;left:707px;top:88px;width:235px;height:28px;background:var(--white);font-size:10px;color:#999;padding:6px 10px}
.newsletter-btn{position:absolute;left:942px;top:88px;width:70px;height:28px;background:var(--white);border-left:1px solid #ccc;color:var(--black);font-size:10px;font-weight:700;text-align:center;line-height:28px}
.social{position:absolute;left:712px;top:138px;display:flex;gap:22px}
.social span{width:16px;height:16px;border-radius:50%;background:var(--white);display:block}
.f-rule{position:absolute;left:171px;top:222px;width:858px;height:1px;background:#333}
.copyright{position:absolute;left:0;top:240px;width:1200px;text-align:center;font-size:10px;color:#aaa}
</style>
</head>
<body>

<header class="site-header">
  <div class="brand"><span>VELMOT</span><span class="brand-mark"></span></div>
  <nav class="main-nav">
    <span class="active">HOME</span><span>MARLOES</span><span>SKILLS</span><span>EXPERIENCE</span><span>PORTFOLIO</span><span>EDUCATION</span><span>CONTACT</span>
  </nav>
</header>

<section class="hero">
  <div class="photo" role="img" aria-label="Black and white portrait of Pieter"></div>
  <h1 class="person-name" style="top:190px">PIETER</h1>
  <p class="person-bio" style="top:268px">Interim manager and consultant in accounting and finance, helping small and medium businesses get their numbers in order. Clear reporting, steady control and honest advice, from month end closing to board level planning. Working with teams to build simple processes that last, and to bring calm to complex financial questions in a short time.</p>
</section>

<section class="experience">
  <h2 class="section-title" style="top:52px">EXPERIENCE</h2>
  <div class="timeline-line"></div>

  <div class="tl-label" style="left:420px;top:164px">Accounting 2012</div>
  <div class="tl-icon" style="top:155px"><svg width="18" height="18" viewBox="0 0 18 18"><rect x="3" y="2" width="12" height="14" fill="none" stroke="#333" stroke-width="1.5"/><line x1="6" y1="6" x2="12" y2="6" stroke="#333"/><line x1="6" y1="9" x2="12" y2="9" stroke="#333"/><line x1="6" y1="12" x2="12" y2="12" stroke="#333"/></svg></div>
  <p class="tl-text" style="left:668px;top:153px">Led the accounting team through a full system change, closing books on time each month.</p>

  <p class="tl-text" style="left:165px;top:225px;text-align:right">Guided cross team projects and shared reporting duties with department heads in a fast growing firm.</p>
  <div class="tl-icon" style="top:242px"><svg width="18" height="18" viewBox="0 0 18 18"><circle cx="6" cy="6" r="3" fill="none" stroke="#333" stroke-width="1.5"/><circle cx="12" cy="6" r="3" fill="none" stroke="#333" stroke-width="1.5"/><path d="M1 16c0-4 10-4 10 0M7 16c0-4 10-4 10 0" fill="none" stroke="#333" stroke-width="1.5"/></svg></div>
  <div class="tl-label" style="left:645px;top:251px">Team player 2013</div>

  <div class="tl-label" style="left:404px;top:339px">Trouble shooter 2014</div>
  <div class="tl-icon" style="top:330px"><svg width="18" height="18" viewBox="0 0 18 18"><path d="M2 9l14-6-6 14-2-6z" fill="none" stroke="#333" stroke-width="1.5"/></svg></div>
  <p class="tl-text" style="left:668px;top:328px">Solved urgent finance issues for clients in transition and set up clear control steps.</p>

  <p class="tl-text" style="left:165px;top:400px;text-align:right">Managed budgets and planning for several projects, reporting progress straight to the board.</p>
  <div class="tl-icon" style="top:417px"><svg width="18" height="18" viewBox="0 0 18 18"><rect x="2" y="5" width="14" height="10" fill="none" stroke="#333" stroke-width="1.5"/><rect x="6" y="2" width="6" height="3" fill="none" stroke="#333" stroke-width="1.5"/></svg></div>
  <div class="tl-label" style="left:645px;top:426px">Project management 2015</div>

  <div class="tl-label" style="left:395px;top:514px">Financial Reporter 2016</div>
  <div class="tl-icon" style="top:505px"><svg width="18" height="18" viewBox="0 0 18 18"><polyline points="2,15 7,9 10,12 16,4" fill="none" stroke="#333" stroke-width="1.5"/><line x1="2" y1="16" x2="16" y2="16" stroke="#333" stroke-width="1.5"/></svg></div>
  <p class="tl-text" style="left:668px;top:503px">Prepared monthly and yearly financial reports for owners, banks and auditors.</p>
</section>

<section class="jobs">
  <h2 class="section-title jobs-title" style="top:60px;font-weight:400">PIETER <span>JOBS</span></h2>

  <h3 class="col-title" style="left:171px;top:146px">ACTUAL JOBS</h3>
  <div class="col-line" style="left:325px;top:190px;height:290px"></div>
  <div class="job-name" style="left:171px;top:222px">Advisor Korvex</div>
  <div class="job-dot" style="left:320px;top:226px"></div>
  <p class="job-text" style="left:353px;top:200px">Advising the board on finance and risk, with focus on clear monthly reporting and control.</p>
  <div class="job-name" style="left:171px;top:302px">Advisor<br>Tenmark</div>
  <div class="job-dot" style="left:320px;top:312px"></div>
  <p class="job-text" style="left:353px;top:290px">Support for owners on budgets, cash flow and planning. Short lines and practical answers for every question that comes up.</p>

  <h3 class="col-title" style="left:630px;top:146px">FINISHED JOBS</h3>
  <div class="col-line" style="left:787px;top:190px;height:290px"></div>
  <div class="job-name" style="left:630px;top:214px">Controller<br>a.i. Korvex</div>
  <div class="job-dot" style="left:782px;top:226px"></div>
  <p class="job-text" style="left:815px;top:200px">Interim controller during a reorganisation, setting up new reporting and closing steps.</p>
  <div class="job-name" style="left:630px;top:300px">Advisor Delta<br>Groen</div>
  <div class="job-dot" style="left:782px;top:312px"></div>
  <p class="job-text" style="left:815px;top:290px">Financial advice for an energy firm, from forecast models to investment cases for the board.</p>
  <div class="job-name" style="left:630px;top:386px">Financial<br>director Halvan</div>
  <div class="job-dot" style="left:782px;top:398px"></div>
  <p class="job-text" style="left:815px;top:376px">Full responsibility for finance, tax and audit over a period of growth and change.</p>
</section>

<section class="skills">
  <h2 class="section-title" style="top:52px">SKILLS</h2>
  <p class="intro" style="top:105px">A short overview of the skills built over years of work in finance and accounting for small and medium businesses, in many sectors and roles.</p>

  <div class="skill-label" style="left:171px;top:180px">ANNUAL REPORTING</div>
  <div class="skill-bar" style="left:171px;top:198px"><div class="track"></div><div class="tip"></div><div class="fill" style="width:290px"></div><span class="pct" style="left:310px">80%</span></div>
  <div class="skill-label" style="left:171px;top:247px">FINANCIAL MONTHLY REPORTING</div>
  <div class="skill-bar" style="left:171px;top:265px"><div class="track"></div><div class="tip"></div><div class="fill" style="width:220px"></div><span class="pct" style="left:310px">60%</span></div>
  <div class="skill-label" style="left:171px;top:314px">ACCOUNTING</div>
  <div class="skill-bar" style="left:171px;top:332px"><div class="track"></div><div class="tip"></div><div class="fill" style="width:325px"></div><span class="pct" style="left:332px">90%</span></div>
  <div class="skill-label" style="left:171px;top:381px">FINANCIAL MANAGEMENT</div>
  <div class="skill-bar" style="left:171px;top:399px"><div class="track"></div><div class="tip"></div><div class="fill" style="width:245px"></div><span class="pct" style="left:310px">75%</span></div>

  <div class="skill-label" style="left:640px;top:180px">PROJECT MANAGEMENT</div>
  <div class="skill-bar" style="left:640px;top:198px"><div class="track"></div><div class="tip"></div><div class="fill" style="width:260px"></div><span class="pct" style="left:315px">70%</span></div>
  <div class="skill-label" style="left:640px;top:247px">TEAM PLAYER</div>
  <div class="skill-bar" style="left:640px;top:265px"><div class="track"></div><div class="tip"></div><div class="fill" style="width:290px"></div><span class="pct" style="left:315px">80%</span></div>
  <div class="skill-label" style="left:640px;top:314px">TROUBLE SHOOTER</div>
  <div class="skill-bar" style="left:640px;top:332px"><div class="track"></div><div class="tip"></div><div class="fill" style="width:290px"></div><span class="pct" style="left:315px">80%</span></div>
  <div class="skill-label" style="left:640px;top:381px">ETC.</div>
  <div class="skill-bar" style="left:640px;top:399px"><div class="track"></div><div class="tip"></div><div class="fill" style="width:150px"></div><span class="pct" style="left:315px">30%</span></div>
</section>

<section class="highlights">
  <div class="tile" style="left:171px">
    <svg width="60" height="50" viewBox="0 0 60 50"><path d="M30 8C22 3 10 3 3 6v38c7-3 19-3 27 2 8-5 20-5 27-2V6c-7-3-19-3-27 2z" fill="none" stroke="#fff" stroke-width="1.8"/><line x1="30" y1="8" x2="30" y2="46" stroke="#fff" stroke-width="1.8"/></svg>
    <h4>EDUCATION</h4>
    <p>Orvalis (RA)<br>Lyceum Vijfhoek</p>
  </div>
  <div class="tile" style="left:464px">
    <svg width="56" height="56" viewBox="0 0 56 56"><line x1="8" y1="8" x2="48" y2="48" stroke="#fff" stroke-width="3"/><line x1="48" y1="8" x2="8" y2="48" stroke="#fff" stroke-width="3"/><circle cx="10" cy="10" r="6" fill="none" stroke="#fff" stroke-width="1.8"/><rect x="40" y="40" width="10" height="10" fill="none" stroke="#fff" stroke-width="1.8"/></svg>
    <h4>WORKED FOR</h4>
    <p>Brink Advocaten &amp; Notarissen<br>Verhoek Audit</p>
  </div>
  <div class="tile" style="left:756px">
    <svg width="60" height="50" viewBox="0 0 60 50"><rect x="3" y="3" width="54" height="44" fill="none" stroke="#fff" stroke-width="1.8"/><polyline points="8,40 22,24 32,34 40,26 52,40" fill="none" stroke="#fff" stroke-width="1.8"/><circle cx="42" cy="14" r="4" fill="none" stroke="#fff" stroke-width="1.8"/></svg>
    <h4>OTHER</h4>
    <p>Fotografy</p>
  </div>
</section>

<section class="portfolio">
  <h2 class="section-title" style="top:62px">PORTFOLIO</h2>
  <p class="intro" style="top:112px">A selection of projects and assignments in reporting, planning and control, carried out for clients in finance, energy and services.</p>
  <div class="work" role="img" aria-label="Business documents and charts on a desk" style="left:171px;top:196px;background:linear-gradient(135deg,#9a8a78,#3d3a38)"></div>
  <div class="work" role="img" aria-label="Hand pointing at a rising blue chart" style="left:460px;top:196px;background:linear-gradient(135deg,#8fb2d6,#2c4f7a)"></div>
  <div class="work" role="img" aria-label="Laptop and financial papers" style="left:749px;top:196px;background:linear-gradient(135deg,#c9c5bd,#6d6a64)"></div>
  <div class="work" role="img" aria-label="Tablet with business graphs" style="left:171px;top:430px;background:linear-gradient(135deg,#b7c3cf,#4a5560)"></div>
  <div class="work" role="img" aria-label="Hands typing on a laptop" style="left:460px;top:430px;background:linear-gradient(135deg,#e3dcd2,#8d7f70)"></div>
  <div class="work" role="img" aria-label="Team meeting around a laptop" style="left:749px;top:430px;background:linear-gradient(135deg,#d5dbe2,#4b5a68)"></div>
</section>

<section class="partner">
  <div class="photo" role="img" aria-label="Black and white portrait of Marloes"></div>
  <h1 class="person-name" style="top:90px">MARLOES</h1>
  <p class="person-bio" style="top:145px">Member of boards of commissioners in the energy business, bringing long experience in governance and strategy. Focused on sound oversight, long term value and a clear view on risk. Supporting boards and owners in times of change, with calm judgement and a practical approach to complex choices.</p>
  <div class="btn-dark" style="left:171px;top:318px">VIEW PROFILE</div>
  <div class="notch"></div>
</section>

<section class="contact">
  <h2 class="section-title" style="top:70px">CONTACT</h2>
  <p class="intro" style="top:120px">Questions about interim work, advice or accounting services? Send a message and we will reply within one working day.</p>

  <div class="info-block" style="top:212px">
    <h4><svg width="16" height="18" viewBox="0 0 16 18"><path d="M8 17s6-6 6-10A6 6 0 0 0 2 7c0 4 6 10 6 10z" fill="none" stroke="#333" stroke-width="1.5"/><circle cx="8" cy="7" r="2" fill="#333"/></svg>Address</h4>
    <p>VELMOT BV<br>Lindenlaan 14<br>Postbus 2210<br>1017 AB Amstelveen</p>
  </div>
  <div class="info-block" style="top:336px">
    <h4><svg width="16" height="14" viewBox="0 0 16 14"><rect x="1" y="2" width="14" height="10" fill="none" stroke="#333" stroke-width="1.5"/><polyline points="1,2 8,8 15,2" fill="none" stroke="#333" stroke-width="1.5"/></svg>Email</h4>
    <p>info@velmot.example</p>
  </div>
  <div class="info-block" style="top:410px">
    <h4><svg width="16" height="16" viewBox="0 0 16 16"><path d="M3 1l3 3-2 2c1 2 3 4 5 5l2-2 3 3-2 3C7 15 1 9 1 3z" fill="none" stroke="#333" stroke-width="1.5"/></svg>Phone</h4>
    <p>020 555 0142 / 06 5550 1987</p>
  </div>

  <div class="field" style="top:210px">Name</div>
  <div class="field" style="top:252px">Email</div>
  <div class="field" style="top:294px">Phone</div>
  <div class="field" style="top:337px;height:112px">Message</div>
  <div class="btn-dark" style="left:542px;top:473px">SUBMIT HERE</div>
</section>

<section class="office">
  <div class="photo" role="img" aria-label="Brick office building under a blue sky" style="inset:0"></div>
  <h2 class="office-title">OUR<br>OFFICE</h2>
</section>

<footer class="site-footer">
  <div class="f-col" style="left:171px"><h4>Company</h4><p>Who we are<br>Our story<br>Our partners<br>Our clients<br>Careers</p></div>
  <div class="f-col" style="left:353px"><h4>About</h4><p>Pieter<br>Marloes<br>Services<br>Experience<br>Education</p></div>
  <div class="f-col" style="left:518px"><h4>Links</h4><p>Home<br>Skills<br>Portfolio<br>Contact<br>Privacy</p></div>
  <div class="f-col" style="left:707px"><h4>Newsletter</h4></div>
  <div class="newsletter-input">Email</div>
  <div class="newsletter-btn">SIGN UP</div>
  <div class="social" aria-label="Social links"><span></span><span></span><span></span><span></span></div>
  <div class="f-rule"></div>
  <p class="copyright">© 2016 All Rights Are Reserved Terms of Use | Privacy Policy</p>
</footer>

</body>
</html>
```